Anzeigengestaltung für eine Hausarztpraxis
Zielgruppe
Wir sind eine Hausarztpraxis mit zwei Standorten und suchen eine Ärztin oder einen Arzt zur Anstellung in der klassischen Hausarzt Medizin am Standort Tannwil
Aufgabenstellung
Bitte beachtet den Text im Anhang, der ist schon vorgegeben. (Anzeigentext)
Wir suchen ein ruhiges, hochwertiges Layout für eine Stellenanzeige einer Hausarztpraxis in einem historischen Gebäude.
Der Text steht im Vordergrund, das Design soll zurückhaltend, klar und wertig sein.
Bitte keine Icons, keine bunten Farben, keine verspielten Elemente.
Gerne viel Weissraum, klare Typografie, ruhige Anmutung.
Schrift: Garamond für den Fliesstext (bereits gewählt).
Das Layout soll sowohl als PDF wie auch online funktionieren.
Optional: ein sehr dezentes grafisches Element oder eine ruhige Bildanmutung (z. B. Struktur, Licht, Architekturdetail).

```html
<!DOCTYPE html>
<html lang="de">
<head>
<meta charset="utf-8">
<title>Hausarztpraxis Tannwil – Stellenanzeige</title>
<link rel="stylesheet" href="https://fonts.googleapis.com/css2?family=EB+Garamond:wght@400;500&display=swap">
<style>
  :root {
    --paper: #f6f5f2;
    --haze-light: #fbfbfa;
    --haze-mid: #ecebe7;
    --haze-warm: #e6e2da;
    --stone-light: #f3ead8;
    --stone-mid: #e3d3b3;
    --ink: #2f2f2f;
    --ink-soft: #3a3a3a;
  }
  * { margin: 0; padding: 0; box-sizing: border-box; }
  html, body { width: 1200px; height: 800px; overflow: hidden; background: var(--paper); }
  .ad {
    position: relative;
    width: 1200px;
    height: 800px;
    overflow: hidden;
    font-family: "EB Garamond", Garamond, serif;
    color: var(--ink);
  }
  .ad__backdrop {
    position: absolute;
    inset: 0;
    background:
      radial-gradient(ellipse 520px 260px at 580px 330px, var(--haze-warm) 0%, rgba(230,226,218,0) 70%),
      linear-gradient(180deg, var(--haze-light) 0%, var(--haze-mid) 55%, var(--haze-warm) 100%);
  }
  .ad__detail {
    position: absolute;
    left: 978px;
    top: 38px;
    width: 158px;
    height: 124px;
    border-radius: 50%;
    background: radial-gradient(ellipse at 45% 55%, var(--stone-light) 0%, var(--stone-mid) 100%);
    opacity: 0.85;
  }
  .ad__content {
    position: absolute;
    left: 64px;
    top: 186px;
    width: 1050px;
  }
  .ad__title {
    font-weight: 400;
    font-size: 48px;
    letter-spacing: 0.5px;
    line-height: 48px;
    color: var(--ink);
  }
  .ad__subtitle {
    margin-top: 29px;
    font-weight: 400;
    font-size: 26px;
    line-height: 26px;
    color: var(--ink-soft);
  }
  .ad__body {
    margin-top: 51px;
    font-size: 20px;
    line-height: 26px;
    color: var(--ink-soft);
  }
  .ad__body + .ad__body { margin-top: 24px; }
  .ad__closing {
    margin-top: 54px;
    font-size: 23px;
    line-height: 23px;
    color: var(--ink-soft);
  }
  .ad__contact {
    margin-top: 76px;
    margin-top: 34px;
    font-size: 18px;
    line-height: 18px;
    color: var(--ink-soft);
  }
  .ad__locations {
    margin-top: 43px;
    font-size: 18px;
    line-height: 18px;
    color: var(--ink-soft);
  }
</style>
</head>
<body>
<main class="ad">
  <div class="ad__backdrop" role="img" aria-label="Blasses Foto eines historischen Hauses mit Ziegeldach und Fensterläden, davor ein Hof mit Steinen und Kies"></div>
  <div class="ad__detail" role="img" aria-label="Rundes Detailbild einer hellen Sandsteinmauer im Licht"></div>

  <section class="ad__content">
    <h1 class="ad__title">HAUSARZTPRAXIS TANNWIL</h1>
    <h2 class="ad__subtitle">VERSTÄRKUNG GESUCHT: ÄRZTIN / ARZT (m/w/d)</h2>

    <p class="ad__body">Wir sind eine etablierte Hausarztpraxis mit zwei Standorten und suchen zur Verstärkung unseres engagierten Teams in Tannwil eine Ärztin oder einen Arzt in Teilzeit. Unser Standort in Tannwil liegt in einem historischen Gebäude mit ruhiger Arbeitsatmosphäre und Blick in den Innenhof.</p>

    <p class="ad__body">Wir bieten Ihnen ein vielseitiges Patientengut, flexible Arbeitszeiten, eine freundliche und kollegiale Atmosphäre. Wir legen Wert auf Eigenverantwortung und gegenseitige Unterstützung. Erfahrung in Allgemeinmedizin ist von Vorteil, aber nicht zwingend. Weiterbildungsassistenten sind ebenfalls willkommen. Werden Sie Teil unseres Teams und gestalten Sie die Hausarztmedizin in Tannwil mit.</p>

    <p class="ad__closing">Wir freuen uns auf Ihre Bewerbung</p>
    <p class="ad__contact">Kontakt: Dr. med. [Nachname], E-Mail: kontakt@hausarzt-tannwil.ch, Tel: [Telefonnummer]</p>
    <p class="ad__locations">Standorte: Tannwil &amp; [Zweiter Standortname]</p>
  </section>
</main>
</body>
</html>
```